Ward Compass Business Card Design*

We need a business card design for our company Ward Compass. Our company is specialized in providing online consulting services regarding medical institutions, hospitals and doctors. We work with patients worldwide looking to choose between healthcare providers. We have a website you may use as a reference, where we list doctors and clinics worldwide. So we target Medical providers as well as patients worldwide.
Target Market(s)
Medical Providers and patients around the world
Industry/Entity Type
Medical
Contact Information for Business Card
Salwa Kettani
CEO
+90 612 348 2175
info@wardcompass.example
www.wardcompass.example
14 Annakhil 7 H.R.B. Rabat, Morocco
Requirements
Must have
- Company logo/name on one full side, personal info and smaller logo and company name on the other side.
Nice to have
- Smart and elegant design

```html
<!DOCTYPE html>
<html lang="en">
<head>
<meta charset="utf-8">
<title>Ward Compass Business Card</title>
<link rel="stylesheet" href="https://fonts.googleapis.com/css2?family=Montserrat:wght@400;700&family=Lato:wght@400;700&display=swap">
<style>
  :root {
    --navy: #0f3f87;
    --navy-deep: #0d2f5e;
    --ink: #12305f;
    --grey: #6b6f76;
    --paper: #f4f4f4;
    --backdrop: #2b2b2b;
  }
  * { box-sizing: border-box; margin: 0; padding: 0; }
  html, body {
    width: 1200px; height: 997px; overflow: hidden;
    background: var(--backdrop);
  }
  .sheet {
    width: 1200px; height: 997px;
    display: flex; flex-direction: column; align-items: center; justify-content: center;
    gap: 60px;
  }
  .card {
    position: relative;
    width: 640px; height: 366px;
    border-radius: 22px;
    overflow: hidden;
    box-shadow: 0 18px 40px rgba(0,0,0,.45);
  }
  /* Front */
  .card-front {
    background: var(--navy);
    color: #fff;
    display: flex; flex-direction: column; align-items: center; justify-content: center;
    gap: 34px;
  }
  .brand {
    display: flex; align-items: center; gap: 18px;
    font-family: "Montserrat", sans-serif;
    font-weight: 700;
    letter-spacing: 2px;
    text-transform: uppercase;
  }
  .brand-dot { border-radius: 50%; flex: none; }
  .card-front .brand { font-size: 38px; }
  .card-front .brand-dot { width: 58px; height: 58px; background: #fff; }
  .front-url {
    font-family: "Lato", sans-serif;
    font-size: 15px; letter-spacing: 3px;
  }
  /* Back */
  .card-back { background: var(--paper); }
  .card-back .brand {
    position: absolute; left: 118px; top: 72px;
    font-size: 32px; color: var(--ink);
  }
  .card-back .brand-dot { width: 50px; height: 50px; background: var(--ink); }
  .person {
    position: absolute; left: 118px; top: 196px;
    font-family: "Montserrat", sans-serif; color: var(--ink);
  }
  .person-name { font-size: 19px; font-weight: 700; letter-spacing: .5px; text-transform: uppercase; }
  .person-role { font-size: 13px; font-weight: 700; color: var(--grey); margin-top: 2px; }
  .divider {
    position: absolute; left: 370px; top: 160px;
    width: 2px; height: 72px; background: #9aa0a8;
  }
  .contacts {
    position: absolute; left: 398px; top: 158px;
    list-style: none;
    font-family: "Lato", sans-serif; font-size: 15px; color: var(--grey);
    display: flex; flex-direction: column; gap: 6px;
  }
  .contacts li { display: flex; align-items: center; gap: 12px; }
  .contacts svg { width: 15px; height: 15px; fill: var(--ink); flex: none; }
  .address-band {
    position: absolute; left: 0; right: 0; bottom: 0; height: 96px;
    background: var(--navy-deep);
    display: flex; align-items: center; justify-content: center;
    font-family: "Lato", sans-serif; font-size: 19px; color: #e6ebf3; letter-spacing: .5px;
  }
</style>
</head>
<body>
<main class="sheet">
  <section class="card card-front" aria-label="Card front">
    <div class="brand"><span class="brand-dot"></span><span>Ward Compass</span></div>
    <p class="front-url">www.wardcompass.example</p>
  </section>

  <section class="card card-back" aria-label="Card back">
    <div class="brand"><span class="brand-dot"></span><span>Ward Compass</span></div>
    <div class="person">
      <p class="person-name">Salwa Kettani</p>
      <p class="person-role">CEO</p>
    </div>
    <span class="divider"></span>
    <ul class="contacts">
      <li>
        <svg viewBox="0 0 16 16"><path d="M3 1h3l1.5 4-2 1.3a9 9 0 0 0 4.2 4.2L11 8.5l4 1.5v3a2 2 0 0 1-2 2A13 13 0 0 1 1 3a2 2 0 0 1 2-2z"/></svg>
        +90 612 348 2175
      </li>
      <li>
        <svg viewBox="0 0 16 16"><path d="M1 3h14v10H1z M1 3l7 6 7-6" fill="none" stroke="#12305f" stroke-width="1.6"/></svg>
        info@wardcompass.example
      </li>
      <li>
        <svg viewBox="0 0 16 16"><circle cx="8" cy="8" r="6.5" fill="none" stroke="#12305f" stroke-width="1.5"/><path d="M1.5 8h13M8 1.5c-3 3.5-3 9.5 0 13M8 1.5c3 3.5 3 9.5 0 13" fill="none" stroke="#12305f" stroke-width="1.2"/></svg>
        www.wardcompass.example
      </li>
    </ul>
    <div class="address-band">14 Annakhil 7 H.R.B. Rabat, Morocco</div>
  </section>
</main>
</body>
</html>
```